Keystone Trench Co Business Card*

Looking for a professional, clean and crisp business card

I am in the underground utilities industry and am just looking for a really impressive business card. I would like our card to be white with our symbol crisp and clear with it protruding. I also have a business partner that will require his name and info on the card once the design is set. I would like to have our website info on the card which is;
http://keystonetrenchco.example/

Contact Information for Business Card

Website, contact name, number and email

```html
<!DOCTYPE html>
<html lang="en">
<head>
<meta charset="utf-8">
<title>Keystone Trench Co — Business Card</title>
<link rel="stylesheet" href="https://fonts.googleapis.com/css2?family=Roboto:wght@400;500;700&display=swap">
<style>
  :root {
    --stage: #e4e4e4;
    --card: #2d2d2e;
    --card-edge: #3f66c4;
    --ink-light: #f2f2f2;
    --ink-muted: #b9b9bb;
    --accent: #3f66c4;
    --rule: #8a8a8c;
    --scene-dark: #2f2f30;
    --scene-light: #4a4a4c;
  }
  * { box-sizing: border-box; margin: 0; padding: 0; }
  html, body { width: 1200px; height: 801px; overflow: hidden; }
  body {
    background: var(--stage);
    font-family: "Roboto", Arial, sans-serif;
    display: flex;
    align-items: center;
    justify-content: center;
    gap: 40px;
  }
  .card {
    position: relative;
    width: 540px;
    height: 309px;
    background: var(--card);
    border-bottom: 3px solid var(--card-edge);
    overflow: hidden;
  }

  /* Contact side */
  .card-back .scene-faint {
    position: absolute;
    left: 0; right: 0; bottom: 0;
    height: 150px;
    background: linear-gradient(180deg, rgba(255,255,255,0) 0%, rgba(255,255,255,0.03) 100%);
  }
  .card-back .brand {
    position: absolute;
    top: 48px;
    right: 40px;
    display: flex;
    align-items: center;
    gap: 12px;
    color: var(--ink-light);
    font-weight: 700;
    font-size: 22px;
    letter-spacing: 0.5px;
  }
  .brand-dot {
    width: 14px; height: 14px;
    border-radius: 50%;
    background: var(--ink-light);
  }
  .card-back .identity {
    position: absolute;
    left: 40px;
    top: 160px;
  }
  .identity .person-name {
    color: var(--accent);
    font-size: 22px;
    font-weight: 500;
  }
  .identity .person-role {
    color: var(--ink-muted);
    font-size: 13px;
    margin-top: 2px;
  }
  .card-back .divider {
    position: absolute;
    left: 40px; right: 30px;
    top: 213px;
    height: 1px;
    background: var(--rule);
  }
  .card-back .contact-list {
    position: absolute;
    left: 40px;
    top: 224px;
    list-style: none;
  }
  .contact-list li {
    display: flex;
    align-items: center;
    gap: 10px;
    color: var(--ink-muted);
    font-size: 13px;
    line-height: 22px;
  }
  .contact-list svg { width: 12px; height: 12px; flex: none; }

  /* Brand side */
  .card-front .brand-main {
    position: absolute;
    top: 78px;
    left: 0; right: 0;
    text-align: center;
    color: var(--ink-light);
    font-weight: 700;
    font-size: 38px;
    letter-spacing: 1px;
  }
  .card-front .scene-area {
    position: absolute;
    left: 0; right: 0; bottom: 0;
    height: 150px;
    background: linear-gradient(180deg, var(--scene-dark) 0%, var(--scene-light) 100%);
  }
</style>
</head>
<body>

  <section class="card card-back" aria-label="Business card contact side">
    <div class="scene-faint" role="img" aria-label="Faint mountain range illustration"></div>
    <div class="brand"><span class="brand-dot"></span>Keystone Trench Co</div>
    <div class="identity">
      <p class="person-name">Dale Marwick</p>
      <p class="person-role">Owner</p>
    </div>
    <div class="divider"></div>
    <ul class="contact-list">
      <li>
        <svg viewBox="0 0 12 12" aria-hidden="true"><path d="M2.5 1 L4.5 1 L5 3.5 L3.8 4.5 Q5 7 7.5 8.2 L8.5 7 L11 7.5 L11 9.5 Q10.5 11 9 11 Q1 10 1 2.5 Q1 1 2.5 1 Z" fill="var(--accent)"/></svg>
        604-555-0182(DIGS)
      </li>
      <li>
        <svg viewBox="0 0 12 12" aria-hidden="true"><rect x="1" y="2.5" width="10" height="7" fill="none" stroke="var(--accent)" stroke-width="1.4"/><path d="M1 2.5 L6 6.5 L11 2.5" fill="none" stroke="var(--accent)" stroke-width="1.4"/></svg>
        Dale@keystonetrenchco.example
      </li>
      <li>
        <svg viewBox="0 0 12 12" aria-hidden="true"><circle cx="6" cy="6" r="5" fill="none" stroke="var(--accent)" stroke-width="1.3"/><ellipse cx="6" cy="6" rx="2.2" ry="5" fill="none" stroke="var(--accent)" stroke-width="1"/><path d="M1 6 H11" stroke="var(--accent)" stroke-width="1"/></svg>
        www.keystonetrenchco.example
      </li>
    </ul>
  </section>

  <section class="card card-front" aria-label="Business card brand side">
    <p class="brand-main">Keystone Trench Co</p>
    <div class="scene-area" role="img" aria-label="Grey mountain range illustration"></div>
  </section>

</body>
</html>
```